Accounting business needs business card

I have a business card but need something better. I want the colour changed and the design to be better. I have uploaded a picture of my new sign that is grey in colour, i would like to incorporate these colours.

```html
<!DOCTYPE html>
<html lang="en">
<head>
<meta charset="utf-8">
<title>Levelbook business card</title>
<link href="https://fonts.googleapis.com/css2?family=Montserrat:wght@400;500;700&display=swap" rel="stylesheet">
<style>
  :root {
    --stage: #1f1f21;
    --card-dark: #2c2d31;
    --card-dark-edge: #3a3b40;
    --card-light: #ffffff;
    --ink: #1d1d1f;
    --ink-soft: #3a3a3d;
    --paper-text: #f4f4f4;
    --rule: #2a2a2a;
    --badge-blue: #2aa8df;
    --badge-navy: #1e5aa8;
    --badge-yellow: #f4d020;
    --badge-green: #b9d43a;
  }
  * { margin: 0; padding: 0; box-sizing: border-box; }
  html, body {
    width: 1200px; height: 930px; overflow: hidden;
    background: var(--stage);
    font-family: "Montserrat", sans-serif;
  }
  .canvas { position: relative; width: 1200px; height: 930px; }

  .card {
    position: absolute;
    width: 620px; height: 378px;
    border-radius: 22px;
    overflow: hidden;
  }

  /* Front: dark grey */
  .card--front {
    left: 80px; top: 70px;
    background: linear-gradient(135deg, var(--card-dark-edge), var(--card-dark) 60%);
    display: flex; flex-direction: column; align-items: center; justify-content: center;
    gap: 26px;
  }
  .brand-mark {
    width: 92px; height: 92px;
    border-radius: 50%;
    border: 3px solid currentColor;
  }
  .brand-name {
    font-weight: 500;
    letter-spacing: 0.42em;
    text-transform: uppercase;
    padding-left: 0.42em;
  }
  .card--front .brand { color: var(--paper-text); display: flex; flex-direction: column; align-items: center; gap: 26px; }
  .card--front .brand-name { font-size: 38px; }

  /* Back: white */
  .card--back {
    left: 500px; top: 480px;
    background: var(--card-light);
    color: var(--ink);
  }
  .card--back .brand {
    position: absolute; left: 48px; top: 48px;
    display: flex; flex-direction: column; align-items: center; gap: 14px;
  }
  .card--back .brand-mark { width: 76px; height: 76px; border-width: 2.5px; }
  .card--back .brand-name { font-size: 24px; }

  .person {
    position: absolute; right: 40px; top: 60px;
    width: 300px;
    text-align: right;
  }
  .person__name {
    font-size: 25px; font-weight: 700; letter-spacing: 0.05em;
    text-transform: uppercase;
  }
  .person__creds, .person__role {
    font-size: 13.5px; font-weight: 500; color: var(--ink-soft);
    margin-top: 4px;
  }
  .person__rule { height: 1.5px; background: var(--rule); margin-top: 10px; }

  .badges {
    position: absolute; right: 40px; top: 196px;
    display: flex; align-items: center; gap: 12px;
  }
  .badge-seal { width: 44px; height: 44px; border-radius: 50%; border: 3px solid var(--badge-green); background: #fff; }
  .badge-round { width: 60px; height: 60px; border-radius: 50%; background: var(--badge-blue); }
  .badge-band { display: flex; height: 62px; }
  .badge-band__main { width: 104px; background: var(--badge-navy); }
  .badge-band__side { width: 56px; background: var(--badge-yellow); }

  .contact {
    position: absolute; left: 48px; bottom: 40px;
    width: 300px;
  }
  .contact__rule { height: 1.5px; background: var(--rule); margin-bottom: 12px; }
  .contact__list { list-style: none; }
  .contact__item {
    display: flex; align-items: center; gap: 10px;
    font-size: 17px; font-weight: 400; line-height: 1.5;
  }
  .contact__icon { width: 13px; height: 13px; flex: none; }
</style>
</head>
<body>
<main class="canvas">

  <section class="card card--front" aria-label="Card front">
    <div class="brand">
      <span class="brand-mark" aria-hidden="true"></span>
      <span class="brand-name">Levelbook</span>
    </div>
  </section>

  <section class="card card--back" aria-label="Card back">
    <div class="brand">
      <span class="brand-mark" aria-hidden="true"></span>
      <span class="brand-name">Levelbook</span>
    </div>

    <div class="person">
      <p class="person__name">Liam Porter</p>
      <p class="person__creds">CPA, MTAX, BCOM (Acc &amp; Fin)</p>
      <p class="person__role">Taxation &amp; Business Accountant</p>
      <div class="person__rule"></div>
    </div>

    <div class="badges" aria-label="Memberships and registrations">
      <span class="badge-seal" role="img" aria-label="Registered tax agent badge"></span>
      <span class="badge-round" role="img" aria-label="Accounting software partner badge"></span>
      <span class="badge-band" role="img" aria-label="Professional accounting body badge">
        <span class="badge-band__main"></span><span class="badge-band__side"></span>
      </span>
    </div>

    <div class="contact">
      <div class="contact__rule"></div>
      <ul class="contact__list">
        <li class="contact__item">
          <svg class="contact__icon" viewBox="0 0 16 16" aria-hidden="true"><path d="M4 1.5l2.4 3-1.3 1.6c.8 1.8 2.1 3.1 3.9 3.9l1.6-1.3 3 2.4-1.2 2.6C7 13.5 2.5 9 1.4 2.7z" fill="#1d1d1f"/></svg>
          <span>0412 555 019</span>
        </li>
        <li class="contact__item">
          <svg class="contact__icon" viewBox="0 0 16 16" aria-hidden="true"><rect x="1" y="3" width="14" height="10" fill="none" stroke="#1d1d1f" stroke-width="1.6"/><path d="M1 3.5l7 5.5 7-5.5" fill="none" stroke="#1d1d1f" stroke-width="1.6"/></svg>
          <span>liam@levelbook.com.au</span>
        </li>
        <li class="contact__item">
          <svg class="contact__icon" viewBox="0 0 16 16" aria-hidden="true"><circle cx="8" cy="8" r="6.6" fill="none" stroke="#1d1d1f" stroke-width="1.4"/><ellipse cx="8" cy="8" rx="3" ry="6.6" fill="none" stroke="#1d1d1f" stroke-width="1.2"/><path d="M1.5 8h13" stroke="#1d1d1f" stroke-width="1.2"/></svg>
          <span>www.levelbook.com.au</span>
        </li>
      </ul>
    </div>
  </section>

</main>
</body>
</html>
```